Pet Care Business Card

Dog & Cat Grooming, we come to you or come to Whisker Haven Grooming
Doggy day care,
Boutique holiday care,
Pet Supplies
All Natural Products used
Have created the logo, which I will forward shortly but need help to have it on flyers business cards ect
email whiskerhavengrooming@mailbrook.net
Ph: 0471352706
Colours: Green Black and paws prints nott sure what colour for them
Updates
Thank you to all that forwarded their designs, very hard choice and I thank you for your effort, shall recommend this to all my collegues
Thanks Again Dot :)
Industry/Entity Type
Business
Contact Information for Business Card
0471352706
517 upper Tindale Road
Brookvale QLD 4581

```html
<!DOCTYPE html>
<html lang="en">
<head>
<meta charset="utf-8">
<title>Whisker Haven Grooming – Business Card</title>
<link rel="stylesheet" href="https://fonts.googleapis.com/css2?family=Michroma&family=Roboto+Slab:wght@700&display=swap">
<style>
  :root {
    --page: #e8e8e8;
    --card: #ffffff;
    --brand: #9a4a12;
    --brand-light: #c98d62;
    --ink: #4a4a4a;
    --rule: #9a9a9a;
  }
  * { margin: 0; padding: 0; box-sizing: border-box; }
  html, body {
    width: 1200px; height: 900px; overflow: hidden;
    background: var(--page);
  }
  .card {
    position: absolute; left: 150px; top: 193px;
    width: 900px; height: 514px;
    background: var(--card);
    box-shadow: 0 10px 30px rgba(0,0,0,0.12);
    overflow: hidden;
    font-family: "Michroma", "Arial", sans-serif;
    color: var(--ink);
  }
  .brand-mark {
    position: absolute; left: 245px; top: 75px;
    width: 110px; height: 110px;
    border: 4px solid var(--brand);
    border-radius: 50%;
  }
  .brand-name {
    position: absolute; left: 120px; top: 196px; width: 360px;
    text-align: center;
    font-family: "Roboto Slab", Georgia, serif;
    font-weight: 700; font-size: 32px; line-height: 1;
    color: var(--brand);
    white-space: nowrap;
  }
  .holder {
    position: absolute; right: 470px; top: 262px;
    text-align: right; text-transform: uppercase;
  }
  .holder-name { font-size: 15px; color: var(--brand); letter-spacing: 0.5px; }
  .holder-role { font-size: 11px; margin-top: 8px; }
  .address {
    position: absolute; right: 470px; top: 352px;
    text-align: right; text-transform: uppercase;
    font-size: 11px; line-height: 1.8;
  }
  .divider {
    position: absolute; left: 450px; top: 252px;
    width: 1px; height: 100px; background: var(--rule);
  }
  .contacts {
    position: absolute; left: 470px; top: 252px;
    list-style: none; font-size: 11px;
  }
  .contacts li { display: flex; align-items: center; height: 22px; }
  .contacts li.gap { margin-top: 16px; }
  .contacts svg { width: 14px; height: 14px; margin-right: 8px; flex: none; }
  .contacts .lower { text-transform: uppercase; font-size: 9.5px; }
  .swoosh { position: absolute; left: 0; top: 0; }
</style>
</head>
<body>
  <div class="card">
    <div class="brand-mark"></div>
    <div class="brand-name">Whisker Haven Grooming</div>

    <div class="holder">
      <div class="holder-name">Dot Ainsley</div>
      <div class="holder-role">Owner / C.E.O</div>
    </div>

    <div class="address">
      517 upper Tindale Road,<br>Brookvale QLD 4581
    </div>

    <div class="divider"></div>

    <ul class="contacts">
      <li>
        <svg viewBox="0 0 14 14"><circle cx="7" cy="7" r="7" fill="var(--brand)"/><path d="M4.5 3.5 l1.5 0 l0.6 2 l-1 0.8 q0.8 1.6 2.1 2.1 l0.8 -1 l2 0.6 l0 1.5 q-4.5 0.5 -6 -6 z" fill="#fff"/></svg>
        0471352706
      </li>
      <li>
        <svg viewBox="0 0 14 14"><circle cx="7" cy="7" r="7" fill="var(--brand)"/><rect x="4.5" y="3" width="5" height="8" rx="1" fill="#fff"/></svg>
        0471880213
      </li>
      <li>
        <svg viewBox="0 0 14 14"><circle cx="7" cy="7" r="7" fill="var(--brand)"/><rect x="3.5" y="4.5" width="7" height="5" fill="#fff"/></svg>
        0754829160
      </li>
      <li class="gap">
        <svg viewBox="0 0 14 14"><circle cx="7" cy="7" r="7" fill="var(--brand)"/><rect x="3.5" y="4.5" width="7" height="5" fill="#fff"/><path d="M3.5 4.5 L7 7.3 L10.5 4.5" stroke="var(--brand)" stroke-width="0.8" fill="none"/></svg>
        <span class="lower">whiskerhavengrooming@mailbrook.net</span>
      </li>
      <li>
        <svg viewBox="0 0 14 14"><circle cx="7" cy="7" r="7" fill="var(--brand)"/><circle cx="7" cy="7" r="3.6" fill="none" stroke="#fff" stroke-width="1"/><path d="M3.4 7 H10.6 M7 3.4 V10.6" stroke="#fff" stroke-width="0.8"/></svg>
        <span class="lower">www.whiskerhaven.net</span>
      </li>
    </ul>

    <svg class="swoosh" width="900" height="514" viewBox="0 0 900 514">
      <path d="M0 514 C 320 500 640 440 900 325" fill="none" stroke="var(--brand-light)" stroke-width="5"/>
      <path d="M0 514 C 330 508 650 452 900 340 L 900 420 C 700 480 380 512 0 514 Z" fill="var(--brand)"/>
    </svg>
  </div>
</body>
</html>
```